BOLD PINE HEATING AND COOLING

Industry/Entity Type

Hvac

Requirements
Must have
• logo
My name: Gavin Pruszynski
Phone number 555-309-4461
Text:
Furnace and AC repairs
New furnace and AC installation
Ductwork
Gas lines
Water Tanks
Tankless water heaters
Nice to have
• Profesional modern look

```html
<!DOCTYPE html>
<html lang="en">
<head>
<meta charset="utf-8">
<title>Bold Pine Heating and Cooling – Business Card</title>
<link rel="stylesheet" href="https://fonts.googleapis.com/css2?family=Montserrat:wght@400;500;600&family=Oswald:wght@600&display=swap">
<style>
  :root {
    --backdrop: #121212;
    --card: #242424;
    --card-edge: #2c2c2c;
    --silver: #c4c4c4;
    --silver-soft: #a8a8a8;
  }
  * { box-sizing: border-box; margin: 0; padding: 0; }
  html, body { width: 1200px; height: 900px; overflow: hidden; }
  body {
    background: var(--backdrop);
    display: flex;
    flex-direction: column;
    align-items: center;
    justify-content: center;
    gap: 40px;
    font-family: "Montserrat", sans-serif;
    color: var(--silver);
  }
  .card {
    width: 660px;
    height: 377px;
    background: linear-gradient(160deg, var(--card-edge), var(--card));
    position: relative;
    display: flex;
    flex-direction: column;
    align-items: center;
  }
  .brand {
    display: flex;
    align-items: center;
    gap: 14px;
  }
  .brand-mark {
    width: 14px;
    height: 14px;
    background: var(--silver);
  }
  .brand-name {
    font-family: "Montserrat", sans-serif;
    font-weight: 600;
    color: var(--silver);
    letter-spacing: 0.08em;
    line-height: 1.25;
    text-transform: uppercase;
  }
  .card-front .brand { margin-top: 110px; }
  .card-front .brand-name { font-size: 30px; text-align: center; }
  .card-front .brand-name small { display: block; font-size: 15px; font-weight: 600; letter-spacing: 0.12em; }
  .services {
    margin-top: 44px;
    text-align: center;
    font-size: 15px;
    line-height: 1.5;
    color: var(--silver);
  }
  .card-back .brand { margin-top: 70px; }
  .card-back .brand-name { font-size: 30px; }
  .card-back .brand-name small { display: block; font-size: 15px; font-weight: 600; letter-spacing: 0.12em; }
  .contact-row {
    margin-top: 70px;
    display: flex;
    align-items: center;
    gap: 40px;
  }
  .person { text-align: right; }
  .person-name {
    font-family: "Oswald", sans-serif;
    font-weight: 600;
    font-size: 30px;
    letter-spacing: 0.01em;
    text-transform: uppercase;
    color: var(--silver-soft);
  }
  .person-role { font-size: 17px; color: var(--silver-soft); margin-top: 2px; }
  .divider { width: 2px; height: 90px; background: var(--silver-soft); }
  .details { list-style: none; font-size: 19px; line-height: 1.55; }
  .details li { display: flex; align-items: center; gap: 12px; }
  .details svg { width: 14px; height: 14px; fill: none; stroke: var(--silver); stroke-width: 1.6; }
</style>
</head>
<body>
  <section class="card card-front">
    <div class="brand">
      <span class="brand-mark"></span>
      <p class="brand-name">Bold Pine<small>Heating and Cooling</small></p>
    </div>
    <p class="services">
      Furnace and AC repairs | New furnace and AC installation<br>
      Ductwork | Gas lines | Water Tanks | Tankless water heaters
    </p>
  </section>

  <section class="card card-back">
    <div class="brand">
      <span class="brand-mark"></span>
      <p class="brand-name">Bold Pine<small>Heating and Cooling</small></p>
    </div>
    <div class="contact-row">
      <div class="person">
        <p class="person-name">Gavin Pruszynski</p>
        <p class="person-role">Director</p>
      </div>
      <span class="divider"></span>
      <ul class="details">
        <li>
          <svg viewBox="0 0 16 16" aria-hidden="true"><path d="M4 2l2.5 3-1.5 1.5c1 2 2.5 3.5 4.5 4.5L11 9.5l3 2.5-1.5 2C7 13.5 2.5 9 2 3.5z"/></svg>
          555-309-4461
        </li>
        <li>
          <svg viewBox="0 0 16 16" aria-hidden="true"><rect x="1.5" y="3.5" width="13" height="9"/><path d="M1.5 3.5L8 9l6.5-5.5"/></svg>
          info@boldpinehvac.com
        </li>
        <li>
          <svg viewBox="0 0 16 16" aria-hidden="true"><circle cx="8" cy="8" r="6.5"/><path d="M1.5 8h13M8 1.5c-3 3.5-3 9.5 0 13M8 1.5c3 3.5 3 9.5 0 13"/></svg>
          www.boldpinehvac.com
        </li>
      </ul>
    </div>
  </section>
</body>
</html>
```